MRT Property - Business Cards

Looking for a business card & general letterhead, signage etc design for our new logo.

Colours:
000a20
0056a2
00b5ef
0088ce
68cef2

Fonts:
Poppins
Karla

Please keep look and feel of new brand - example in the zip package I sent.

```html
<!DOCTYPE html>
<html lang="en">
<head>
<meta charset="utf-8">
<title>MRT Property – Business Cards</title>
<link rel="stylesheet" href="https://fonts.googleapis.com/css2?family=Poppins:wght@300;400;500;600;700&display=swap">
<style>
  :root {
    --ink: #000a20;
    --brand-blue: #0056a2;
    --sky: #00b5ef;
    --mid-blue: #0088ce;
    --pale-sky: #68cef2;
    --paper: #ffffff;
    --backdrop: #222222;
  }
  * { margin: 0; padding: 0; box-sizing: border-box; }
  html, body {
    width: 1200px; height: 780px; overflow: hidden;
    background: var(--backdrop);
    font-family: "Poppins", sans-serif;
  }
  .canvas {
    position: relative; width: 1200px; height: 780px;
    display: flex; align-items: center; justify-content: center; gap: 50px;
  }
  .card {
    position: relative; width: 540px; height: 315px;
    border-radius: 2px; overflow: hidden;
    box-shadow: 0 18px 40px rgba(0,0,0,.55);
  }
  .card-front { background: var(--paper); }
  .front-band { position: absolute; inset: 0; }
  .logo-name {
    position: absolute; top: 46px; right: 40px;
    font-weight: 600; font-size: 36px; color: var(--brand-blue);
    letter-spacing: .5px;
  }
  .person { position: absolute; top: 112px; left: 78px; text-align: right; }
  .person-name { font-size: 25px; line-height: 1; font-weight: 600; color: var(--brand-blue); }
  .person-name .surname { font-weight: 300; color: var(--pale-sky); }
  .person-role { font-size: 12px; font-weight: 500; color: var(--ink); margin-top: 3px; }
  .divider {
    position: absolute; left: 248px; top: 150px;
    width: 1px; height: 62px; background: var(--brand-blue);
  }
  .contact-list {
    position: absolute; left: 266px; top: 150px; list-style: none;
    font-size: 14px; color: var(--ink); line-height: 21px;
  }
  .contact-list li { display: flex; align-items: center; gap: 8px; }
  .contact-list svg { width: 13px; height: 13px; flex: none; }
  .address {
    position: absolute; left: 30px; bottom: 16px;
    font-size: 13px; font-weight: 300; color: var(--paper);
  }
  .card-back { background: var(--brand-blue); }
  .back-pattern {
    position: absolute; inset: 0;
    background: linear-gradient(135deg, #0b3f8f 0%, #0d4fa0 50%, #1e7ccc 80%, #3aa6e4 100%);
  }
  .back-logo-name {
    position: absolute; right: 70px; bottom: 66px;
    font-size: 17px; font-weight: 600; color: var(--paper);
  }
</style>
</head>
<body>
<main class="canvas">
  <section class="card card-front" aria-label="Business card front">
    <svg class="front-band" viewBox="0 0 540 315" preserveAspectRatio="none" aria-hidden="true">
      <path d="M0,178 Q110,300 540,272 L540,315 L0,315 Z" fill="var(--brand-blue)"/>
      <path d="M10,168 Q118,288 540,262" fill="none" stroke="var(--paper)" stroke-width="5"/>
      <path d="M14,164 Q124,282 540,257" fill="none" stroke="var(--pale-sky)" stroke-width="3"/>
    </svg>
    <div class="logo-name">MRT Property</div>
    <div class="person">
      <div class="person-name">Lachlan <span class="surname">Reid</span></div>
      <div class="person-role">Director</div>
    </div>
    <div class="divider"></div>
    <ul class="contact-list">
      <li>
        <svg viewBox="0 0 16 16" aria-hidden="true"><path d="M4 1l3 3-2 2c1 2 3 4 5 5l2-2 3 3-2 2C7 14 2 9 2 3z" fill="var(--mid-blue)"/></svg>
        +61 2 9000 1234
      </li>
      <li>
        <svg viewBox="0 0 16 16" aria-hidden="true"><circle cx="8" cy="8" r="6.5" fill="none" stroke="var(--mid-blue)" stroke-width="1.6"/><path d="M1.5 8h13M8 1.5c3 3 3 10 0 13M8 1.5c-3 3-3 10 0 13" fill="none" stroke="var(--mid-blue)" stroke-width="1.2"/></svg>
        www.mrtproperty.com.au
      </li>
      <li>
        <svg viewBox="0 0 16 16" aria-hidden="true"><rect x="1" y="3" width="14" height="10" rx="1" fill="none" stroke="var(--mid-blue)" stroke-width="1.6"/><path d="M1.5 4l6.5 5 6.5-5" fill="none" stroke="var(--mid-blue)" stroke-width="1.4"/></svg>
        info@mrtproperty.com.au
      </li>
    </ul>
    <p class="address">Suite 4.12, Level 4, 18 Harbour Lane, Rivermead NSW 2190</p>
  </section>

  <section class="card card-back" aria-label="Business card back">
    <div class="back-pattern" role="img" aria-label="Repeating brand pattern in deep and light blue tones"></div>
    <div class="back-logo-name">MRT Property</div>
  </section>
</main>
</body>
</html>
```